Business Card Design

Online clothing womens clothing store, I sell my clothing online and at the markets.

i would like the attached picture on the front of the card and the contact information on the back.

Industry/Entity Type

Business

Contact Information for Business Card

Marlow Thread
Karen Whitfield
(Instagram symbol) _marlow_thread_
(Facebook symbol) www.fakebookexample.com/marlowthreadau/

W : www.marlowthread.example.au
E : info@marlowthread.example.au
P : 0498716204

```html
<!DOCTYPE html>
<html lang="en">
<head>
<meta charset="utf-8">
<title>Marlow Thread – Business Card</title>
<link rel="stylesheet" href="https://fonts.googleapis.com/css2?family=Special+Elite&family=Marcellus+SC&family=Arimo&display=swap">
<style>
  :root {
    --page: #e4e2df;
    --ink: #111111;
    --panel: #0d0d0d;
    --paper: #ffffff;
    --smoke-light: #d9d9d9;
    --smoke-mid: #a9a9a9;
    --smoke-dark: #5c5c5c;
    --mist-teal: #b9cfcc;
    --mist-grey: #8d8f96;
    --band: rgba(255, 255, 255, 0.62);
  }
  html, body {
    margin: 0;
    width: 1200px;
    height: 892px;
    overflow: hidden;
    background: var(--page);
  }
  .sheet {
    position: relative;
    width: 1200px;
    height: 892px;
  }
  .card {
    position: absolute;
    left: 290px;
    width: 620px;
    height: 379px;
    overflow: hidden;
    box-shadow: 0 6px 18px rgba(0, 0, 0, 0.18);
  }
  .card--front { top: 47px; }
  .card--back { top: 466px; background: var(--panel); }

  /* front */
  .front-photo {
    position: absolute;
    inset: 0;
    background:
      radial-gradient(ellipse 45% 70% at 72% 62%, var(--smoke-dark) 0%, rgba(92, 92, 92, 0.55) 45%, rgba(92, 92, 92, 0) 80%),
      linear-gradient(100deg, var(--smoke-light) 0%, #cfcfcf 45%, var(--smoke-mid) 100%);
  }
  .front-brand {
    position: absolute;
    left: 96px;
    right: 24px;
    top: 236px;
    margin: 0;
    font-family: "Special Elite", monospace;
    font-weight: 400;
    font-size: 52px;
    letter-spacing: 1px;
    line-height: 1;
    color: var(--paper);
    white-space: nowrap;
    text-align: right;
  }

  /* back */
  .back-photo {
    position: absolute;
    left: 0;
    top: 0;
    width: 288px;
    height: 379px;
    background:
      radial-gradient(ellipse 40% 55% at 55% 55%, #4f5560 0%, rgba(79, 85, 96, 0.4) 55%, rgba(79, 85, 96, 0) 85%),
      linear-gradient(180deg, #dfe8e6 0%, var(--mist-teal) 35%, #c8cbd2 70%, var(--mist-grey) 100%);
  }
  .brand-band {
    position: absolute;
    left: 0;
    top: 112px;
    width: 288px;
    height: 74px;
    background: var(--band);
    display: flex;
    align-items: center;
    justify-content: center;
  }
  .brand-band__name {
    margin: 0;
    font-family: "Special Elite", monospace;
    font-weight: 400;
    font-size: 24px;
    letter-spacing: 2px;
    color: var(--ink);
    white-space: nowrap;
  }
  .contact-panel {
    position: absolute;
    left: 288px;
    top: 0;
    right: 0;
    bottom: 0;
    padding: 52px 0 0 30px;
    color: var(--paper);
  }
  .contact-panel__name {
    margin: 0 0 42px;
    font-family: "Marcellus SC", serif;
    font-weight: 400;
    font-size: 25px;
    letter-spacing: 5px;
    white-space: nowrap;
  }
  .contact-list {
    list-style: none;
    margin: 0;
    padding: 0;
    font-family: "Arimo", sans-serif;
    font-size: 17px;
  }
  .contact-list li {
    display: flex;
    align-items: center;
    gap: 14px;
    height: 30px;
    white-space: nowrap;
  }
  .contact-icon {
    flex: none;
    width: 18px;
    height: 18px;
    box-sizing: border-box;
  }
  .contact-icon--ring {
    border: 2px solid var(--paper);
    border-radius: 50%;
  }
</style>
</head>
<body>
<main class="sheet">

  <section class="card card--front" aria-label="Card front">
    <div class="front-photo" role="img" aria-label="Grey smoky photograph of a figure reaching out through smoke"></div>
    <h1 class="front-brand">MARLOW THREAD</h1>
  </section>

  <section class="card card--back" aria-label="Card back">
    <div class="back-photo" role="img" aria-label="Misty teal and grey photograph of a figure in smoke with outstretched hands"></div>
    <div class="brand-band">
      <p class="brand-band__name">MARLOW THREAD</p>
    </div>

    <div class="contact-panel">
      <h2 class="contact-panel__name">Karen Whitfield</h2>
      <ul class="contact-list">
        <li>
          <svg class="contact-icon" viewBox="0 0 18 18" aria-hidden="true">
            <rect x="0" y="0" width="18" height="18" rx="2" fill="#fff"/>
            <path d="M5 4.5c1 0 1.5 2 1.5 2.5s-1 1-1 1.3c.5 1.5 1.8 2.8 3.2 3.2.3 0 .8-1 1.3-1s2.5.5 2.5 1.5-1 2-2 2C7.5 14 4 10.5 4 6.5c0-1 .5-2 1-2z" fill="#0d0d0d"/>
          </svg>
          <span>0498716204</span>
        </li>
        <li>
          <span class="contact-icon contact-icon--ring" aria-hidden="true"></span>
          <span>marlowthreadau</span>
        </li>
        <li>
          <span class="contact-icon contact-icon--ring" aria-hidden="true"></span>
          <span>marlow_thread</span>
        </li>
        <li>
          <svg class="contact-icon" viewBox="0 0 18 18" aria-hidden="true">
            <rect x="0" y="0" width="18" height="18" rx="2" fill="#fff"/>
            <circle cx="9" cy="9" r="5.5" fill="none" stroke="#0d0d0d" stroke-width="1.3"/>
            <ellipse cx="9" cy="9" rx="2.3" ry="5.5" fill="none" stroke="#0d0d0d" stroke-width="1.1"/>
            <line x1="3.5" y1="9" x2="14.5" y2="9" stroke="#0d0d0d" stroke-width="1.1"/>
          </svg>
          <span>www.marlowthread.example.au</span>
        </li>
        <li>
          <svg class="contact-icon" viewBox="0 0 18 18" aria-hidden="true">
            <rect x="0" y="0" width="18" height="18" rx="2" fill="#fff"/>
            <rect x="3.5" y="5" width="11" height="8" fill="none" stroke="#0d0d0d" stroke-width="1.3"/>
            <polyline points="3.5,5 9,9.5 14.5,5" fill="none" stroke="#0d0d0d" stroke-width="1.3"/>
          </svg>
          <span>info@marlowthread.example.au</span>
        </li>
      </ul>
    </div>
  </section>

</main>
</body>
</html>
```